Nanny Share Ecommerce Website for Finding Childcare and Parents who need Childcare BrightPramHub.net

Our company needs an ecommerce website (BrightPramHub.net) for a US subscription based service strictly for nanny sharing that connects families and caregivers. The website would allow families to connect with one another as well as to search for nannies. The service would be searchable for other families by location (by radius or zip code), children demographic (age range/gender/special needs), days of week or times, after school care, school closure days (holidays), etc. The service would also be searchable for nannies based on gender, provider age range, years experience, language, hourly rate, transportation available, certification (CPR first aid), education etc. The search fields would be searchable and sortable and allow to connect with the provider (after paying subscription fee). The service would be similar to tendlyfolk.net in that it would allow for families and caregivers to post photos as well as a short bio of the themselves. There would also be a feedback/star rating mechanism to rate caregivers who have performed work for families (viewable to public). The service would be free for nannies to post their bios and only a subscription based service for families to connect with other families or with caregivers (able to view bio but need service to connect). There will be a short bio on the benefits of nanny sharing (reduced cost, increased flexibility for parents, reduced illness, increased socialization with other children vs. sole nanny), as well as Q&A section with best practices.

Target Market(s)

Families, Nannies

Industry/Entity Type

Childcare

Logo Text

Bright Pram Hub

Coding

Coded - Design and coding required

Number of Pages Required

5+ page

Requirements
Must have
• Searchable (need to be able to search for families as well as nannies), responsive, functional, easy to use, add value to families and nannies. Needs to be able to collect payment for subscription.
Nice to have
• Optimized for mobile, SEO optimized

```html
<!DOCTYPE html>
<html lang="en">
<head>
<meta charset="utf-8">
<title>Bright Pram Hub – Build Profiles: Family</title>
<link href="https://fonts.googleapis.com/css2?family=Montserrat:wght@400;500;600;700&family=Open+Sans:wght@400;600&display=swap" rel="stylesheet">
<style>
:root{
  --blue:#1dbff0;
  --pink:#f5457f;
  --ink:#333333;
  --muted:#5b5b5b;
  --panel:#f7f7f7;
  --line:#d6d6d6;
  --field:#cfcfcf;
  --footer:#1f1f1f;
  --white:#ffffff;
}
*{box-sizing:border-box;margin:0;padding:0}
html,body{width:1122px;height:1200px;overflow:hidden;background:var(--white)}
body{position:relative;font-family:"Open Sans",sans-serif;color:var(--ink)}
.top-rule{position:absolute;left:0;top:0;width:100%;height:3px;background:var(--blue)}
.site-header{position:absolute;left:0;top:3px;width:100%;height:96px}
.brand{position:absolute;left:93px;top:30px;display:flex;align-items:center;gap:10px}
.brand-dot{width:34px;height:34px;border-radius:50%;background:var(--blue)}
.brand-name{font-family:"Montserrat",sans-serif;font-weight:700;font-size:26px;color:#111}
.main-nav{position:absolute;right:138px;top:42px;display:flex;gap:33px;font-size:13px;line-height:18px}
.main-nav a{color:#444;text-decoration:none}
.main-nav a.active{color:var(--blue)}
.search-icon{position:absolute;right:92px;top:44px}
.hero{position:absolute;left:0;top:99px;width:100%;height:326px;
  background:linear-gradient(100deg,#8a8d91 0%,#9a8f8a 30%,#a47f72 55%,#9d9aa0 80%,#a9abb0 100%)}
.hero-shade{position:absolute;inset:0;background:rgba(60,60,70,.25)}
.hero h1{position:absolute;left:0;right:0;top:138px;text-align:center;font-family:"Montserrat",sans-serif;
  font-weight:600;font-size:51px;line-height:60px;color:var(--white);letter-spacing:.5px}
.profile-panel{position:absolute;left:91px;top:479px;width:939px;height:428px;background:var(--panel);border:1px solid var(--line)}
.profile-panel h2{position:absolute;left:37px;top:48px;font-family:"Montserrat",sans-serif;font-weight:500;font-size:29px;line-height:36px;color:#333}
.family-avatar{position:absolute;left:58px;top:117px}
.upload-btn{position:absolute;left:39px;top:254px;width:164px;height:30px;border-radius:15px;background:var(--pink);
  color:var(--white);font-family:"Montserrat",sans-serif;font-weight:600;font-size:13px;line-height:30px;text-align:center}
.field-label{position:absolute;font-size:16px;line-height:22px;color:#333;white-space:nowrap}
.input{position:absolute;height:31px;background:var(--white);border:1px solid var(--field)}
.select{position:absolute;height:31px;background:var(--white);border:1px solid var(--field);font-family:"Montserrat",sans-serif;font-size:12.5px;line-height:29px;padding-left:13px;color:#333}
.select svg{position:absolute;right:14px;top:12px}
.blurb{position:absolute;left:241px;top:268px;width:654px;font-family:"Montserrat",sans-serif;font-size:12px;line-height:25px;color:var(--muted)}
.blurb a{color:var(--blue);text-decoration:none;margin-left:8px}
.build-btn{position:absolute;left:756px;top:338px;width:143px;height:35px;background:var(--blue);color:var(--white);
  font-family:"Montserrat",sans-serif;font-weight:500;font-size:16px;line-height:35px;text-align:center}
.footer-rule{position:absolute;left:0;top:960px;width:100%;height:4px;background:var(--blue)}
.site-footer{position:absolute;left:0;top:964px;width:100%;height:236px;background:var(--footer);color:var(--white)}
.social{position:absolute;left:0;right:0;top:58px;display:flex;justify-content:center;gap:4px}
.social span{width:38px;height:38px;border:1.5px solid var(--white);border-radius:50%}
.footer-nav{position:absolute;left:0;right:0;top:122px;display:flex;justify-content:center;gap:18px;font-size:14px}
.copyright{position:absolute;left:0;right:0;top:160px;text-align:center;font-size:12px}
</style>
</head>
<body>
<div class="top-rule"></div>
<header class="site-header">
  <div class="brand"><span class="brand-dot"></span><span class="brand-name">Bright Pram Hub</span></div>
  <nav class="main-nav">
    <a class="active" href="#">Home</a><a href="#">About us</a><a href="#">Services</a><a href="#">How it Works</a><a href="#">FAQ</a><a href="#">Blog</a><a href="#">Contact us</a>
  </nav>
  <svg class="search-icon" width="14" height="14" viewBox="0 0 14 14"><circle cx="5.8" cy="5.8" r="4.3" fill="none" stroke="#f5457f" stroke-width="2"/><line x1="9" y1="9" x2="12.5" y2="12.5" stroke="#f5457f" stroke-width="2.2" stroke-linecap="round"/></svg>
</header>

<section class="hero" role="img" aria-label="Photo of a caregiver and a young child stacking toy blocks">
  <div class="hero-shade"></div>
  <h1>BUILD PROFILES-FAMILY</h1>
</section>

<main class="profile-panel">
  <h2>Let’s Start with the basic Information</h2>
  <svg class="family-avatar" width="126" height="126" viewBox="0 0 126 126" role="img" aria-label="Family photo placeholder">
    <circle cx="63" cy="63" r="59" fill="#e6e6e6" stroke="#000" stroke-width="5"/>
  </svg>
  <div class="upload-btn">Upload Family photo</div>

  <span class="field-label" style="left:240px;top:124px">Location</span>
  <div class="input" style="left:318px;top:118px;width:575px"></div>

  <span class="field-label" style="left:240px;top:172px">Number of Children</span>
  <div class="input" style="left:394px;top:166px;width:99px"></div>
  <span class="field-label" style="left:510px;top:172px">Gender of children</span>
  <div class="select" style="left:655px;top:166px;width:238px">Any<svg width="9" height="6" viewBox="0 0 9 6"><path d="M1 1l3.5 3.5L8 1" fill="none" stroke="#333" stroke-width="1.3"/></svg></div>

  <span class="field-label" style="left:240px;top:221px">Age of Children</span>
  <div class="input" style="left:394px;top:215px;width:121px"></div>
  <span class="field-label" style="left:533px;top:221px">Type of Care</span>
  <div class="select" style="left:638px;top:215px;width:255px;padding-left:22px">Any<svg width="9" height="6" viewBox="0 0 9 6"><path d="M1 1l3.5 3.5L8 1" fill="none" stroke="#333" stroke-width="1.3"/></svg></div>

  <p class="blurb">At vero eos et accusamus et iusto odio dignissimos ducimus qui blanditiis praesentium voluptatum deleniti atque corrupti quos dolores et quas molestias excepturi sint occaecati cupiditate non provident, similique sunt in culpa qui officia deserunt mollitia animi, id est laborum <a href="#">.......more</a></p>
  <div class="build-btn">BUILD PROFILE</div>
</main>

<div class="footer-rule"></div>
<footer class="site-footer">
  <div class="social" aria-label="Social links"><span></span><span></span><span></span><span></span><span></span><span></span></div>
  <nav class="footer-nav">
    <span>Home</span><span>/</span><span>About us</span><span>/</span><span>Services</span><span>/</span><span>How it works</span><span>/</span><span>FAQ</span><span>/</span><span>Blog</span><span>/</span><span>Contact us</span>
  </nav>
  <p class="copyright">© Copyright 2018 Bright Pram Hub.All Rights Reserved</p>
</footer>
</body>
</html>
```